Electrician Letterhead Design MVR

We need some letterhead for our bills and other papers.
Customer address is on the right side (Swiss format)
A4 format

Design should also be applicable on Cards

Target Market(s)

Private Customers, Small Business

Industry/Entity Type

Electrician

Other font styles liked:
• incised 901

Colors
00AB8E
00BBA5
67D7C9
C6EFE9
E9F9F6

```html
<!DOCTYPE html>
<html lang="en">
<head>
<meta charset="utf-8">
<title>MVR Letterhead</title>
<link href="https://fonts.googleapis.com/css2?family=Arvo:wght@400;700&display=swap" rel="stylesheet">
<style>
  :root {
    --backdrop: #dcdcdc;
    --paper: #ffffff;
    --brand: #0aa08e;
    --ink: #1a1a1a;
    --faint: #e6e6e6;
    --rule: #9a9a9a;
  }
  * { margin: 0; padding: 0; box-sizing: border-box; }
  html, body {
    width: 1200px; height: 947px; overflow: hidden;
    background: var(--backdrop);
    font-family: "Arvo", serif;
  }
  .letterhead {
    position: absolute; left: 364px; top: 179px;
    width: 472px; height: 605px;
    background: var(--paper);
    overflow: hidden;
  }
  .brand { position: absolute; left: 49px; top: 14px; }
  .brand-name {
    font-family: "Arvo", serif; font-weight: 700;
    font-size: 40px; line-height: 1; color: var(--brand);
    letter-spacing: 1px;
  }
  .brand-tagline {
    margin-top: 3px;
    font-size: 7px; color: var(--ink); letter-spacing: 0.3px;
  }
  .contact {
    position: absolute; left: 318px; top: 24px;
    border-left: 1px solid var(--rule);
    padding-left: 9px;
    font-size: 8.5px; line-height: 11px; color: var(--ink);
  }
  .contact-item { display: flex; align-items: center; gap: 6px; white-space: nowrap; }
  .contact-item svg { width: 8px; height: 8px; flex: none; }
  .watermark {
    position: absolute; left: 68px; top: 222px;
    font-family: "Arvo", serif; font-weight: 700;
    font-size: 140px; line-height: 1; color: var(--faint);
    letter-spacing: 4px;
  }
  .footer-band {
    position: absolute; left: 0; top: 562px;
    width: 452px; height: 20px; background: var(--brand);
    color: #ffffff; font-size: 10px; line-height: 20px;
    text-align: center; padding-right: 20px;
  }
  .footer-arrow { position: absolute; left: 0; top: 0; width: 472px; height: 605px; pointer-events: none; }
</style>
</head>
<body>
  <main class="letterhead">
    <header class="brand">
      <div class="brand-name">MVR</div>
      <div class="brand-tagline">Elektrotechnik Marti GmbH</div>
    </header>

    <address class="contact" style="font-style:normal">
      <div class="contact-item">
        <svg viewBox="0 0 10 10" aria-hidden="true"><rect x="0.5" y="0.5" width="9" height="9" rx="1.5" fill="none" stroke="var(--brand)"/><path d="M3 2.5 L4.2 2.5 L4.6 4 L3.9 4.6 Q4.6 6 5.6 6.3 L6.2 5.6 L7.5 6 L7.5 7.3 Q4 7.5 3 2.5Z" fill="var(--brand)"/></svg>
        <span>044-123 456 789</span>
      </div>
      <div class="contact-item">
        <svg viewBox="0 0 10 10" aria-hidden="true"><rect x="0.5" y="2" width="9" height="6" fill="var(--brand)"/><path d="M0.5 2 L5 5.5 L9.5 2" fill="none" stroke="#fff" stroke-width="0.8"/></svg>
        <span>info@webname.com</span>
      </div>
      <div class="contact-item">
        <svg viewBox="0 0 10 10" aria-hidden="true"><g fill="none" stroke="var(--brand)" stroke-width="0.8"><circle cx="5" cy="5" r="4.3"/><ellipse cx="5" cy="5" rx="1.8" ry="4.3"/><path d="M0.7 5 H9.3 M1.5 2.8 H8.5 M1.5 7.2 H8.5"/></g></svg>
        <span>www.websitename.com</span>
      </div>
    </address>

    <div class="watermark" aria-hidden="true">MVR</div>

    <footer class="footer-band">Your Address line here, Country Code 0123456</footer>
    <svg class="footer-arrow" viewBox="0 0 472 605" aria-hidden="true">
      <polygon points="419,542 437,542 470,572 437,603 419,603 451,572" fill="var(--brand)"/>
    </svg>
  </main>
</body>
</html>
```